Business Card for Coastal Tundrabridge Advisory

We need a business card for Coastal Tundrabridge Advisory. The company website address is provided below. The company logo is attached. We provide specialized permafrost services to the mining, transportation, and oil & gas industries. The card should be prepared for:
Matthias Korhonen, PhD.
Coastal Tundrabridge Advisory
PO Box 418259
Quillwater, Alaska 99642
Direct: +1-907-555-0143
Email: mkorhonen@tundrabridgeadvisory.example
Website: www.coastaltundrabridgeadvisory.example

```html
<!DOCTYPE html>
<html lang="en">
<head>
<meta charset="utf-8">
<title>Coastal Tundrabridge Advisory – Business Card</title>
<link rel="stylesheet" href="https://fonts.googleapis.com/css2?family=Arimo:wght@400;700&display=swap">
<style>
  :root {
    --ink: #0f1820;
    --paper: #f3f3f3;
    --stripe: #505050;
    --backdrop: #e2e2e2;
    --card-w: 644px;
    --card-h: 368px;
  }
  * { box-sizing: border-box; margin: 0; padding: 0; }
  html, body {
    width: 1200px; height: 1040px; overflow: hidden;
    background: var(--backdrop);
    font-family: "Arimo", Arial, sans-serif;
  }
  .canvas { position: relative; width: 1200px; height: 1040px; }
  .card {
    position: absolute; left: 284px;
    width: var(--card-w); height: var(--card-h);
    border-radius: 16px; overflow: hidden;
    box-shadow: 0 2px 4px rgba(0,0,0,.25);
  }
  .card--front { top: 130px; background: var(--paper); }
  .card--back { top: 568px; background: var(--ink); }

  .front-shape { position: absolute; inset: 0; }

  .holder { position: absolute; left: 29px; top: 31px; color: var(--paper); }
  .holder__name { font-size: 23px; font-weight: 700; letter-spacing: .1px; }
  .holder__degree { font-size: 17px; }
  .holder__title { font-size: 16px; margin-top: 1px; margin-left: 1px; }

  .address {
    position: absolute; left: 29px; top: 222px;
    color: var(--paper); font-size: 16px; line-height: 20px;
  }
  .contacts {
    position: absolute; left: 29px; top: 272px;
    list-style: none; color: var(--paper); font-size: 15.5px; line-height: 20.5px;
  }
  .contacts li { display: flex; align-items: center; gap: 8px; }
  .contacts svg { width: 13px; height: 13px; flex: none; fill: var(--paper); }

  .brand {
    position: absolute; text-align: center;
    font-weight: 700; text-transform: uppercase; line-height: 1.25;
  }
  .brand--front {
    left: 330px; width: 300px; top: 164px;
    color: var(--ink); font-size: 16px; letter-spacing: 2.5px;
  }
  .brand--back {
    left: 0; width: 100%; top: 128px;
    color: var(--paper); font-size: 30px; letter-spacing: 4px;
  }
  .back-url {
    position: absolute; left: 0; width: 100%; top: 320px;
    text-align: center; color: var(--paper); font-size: 16px;
  }
</style>
</head>
<body>
<main class="canvas">
  <section class="card card--front" aria-label="Business card front">
    <svg class="front-shape" viewBox="0 0 644 368" preserveAspectRatio="none" aria-hidden="true">
      <polygon points="448,0 460,0 282,184 460,368 448,368 268,184" fill="var(--stripe)"/>
      <polygon points="0,0 443,0 262,184 443,368 0,368" fill="var(--ink)"/>
    </svg>

    <div class="holder">
      <p class="holder__name">Matthias Korhonen, <span class="holder__degree">PhD.</span></p>
      <p class="holder__title">President</p>
    </div>

    <address class="address" style="font-style:normal">
      PO Box 418259<br>
      Quillwater, Alaska 99642
    </address>

    <ul class="contacts">
      <li>
        <svg viewBox="0 0 24 24"><path d="M6.6 10.8a15.1 15.1 0 0 0 6.6 6.6l2.2-2.2c.3-.3.7-.4 1-.2 1.1.4 2.3.6 3.6.6.6 0 1 .4 1 1V20c0 .6-.4 1-1 1A17 17 0 0 1 3 4c0-.6.4-1 1-1h3.5c.6 0 1 .4 1 1 0 1.3.2 2.5.6 3.6.1.3 0 .7-.2 1z"/></svg>
        +1-907-555-0143
      </li>
      <li>
        <svg viewBox="0 0 24 24"><path d="M2 5h20v14H2z M4 7v.4l8 5 8-5V7l-8 5z" fill-rule="evenodd"/></svg>
        mkorhonen@tundrabridgeadvisory.example
      </li>
      <li>
        <svg viewBox="0 0 24 24"><path d="M12 2a10 10 0 1 0 0 20 10 10 0 0 0 0-20zm-1 17.9A8 8 0 0 1 4.2 10.2L9 15v1c0 1.1.9 2 2 2zm6.9-2.5A2 2 0 0 0 16 16h-1v-3c0-.6-.4-1-1-1H8v-2h2c.6 0 1-.4 1-1V7h2c1.1 0 2-.9 2-2v-.4a8 8 0 0 1 2.9 12.8z"/></svg>
        www.coastaltundrabridgeadvisory.example
      </li>
    </ul>

    <p class="brand brand--front">Coastal Tundrabridge<br>Advisory</p>
  </section>

  <section class="card card--back" aria-label="Business card back">
    <p class="brand brand--back">Coastal Tundrabridge<br>Advisory</p>
    <p class="back-url">www.coastaltundrabridgeadvisory.example</p>
  </section>
</main>
</body>
</html>
```